KESTREL Academy Exhibit Booth Posters

My company is KESTREL Academy (a division of KESTREL for Growth). We are exhibiting in a month, and I need to re-do my exhibit booth posters. There will be a total of 4 posters needed. Sizes are below.
1) Top- 11 feet long X 12 inches wide (Try to match color scheme in example photo)
2) Center- 4 feet long X 2 feet wide (Chalkboard background)
3) Left- 18 inches long X 2 feet wide (Cork-board back ground with the use of push pins holding up post-it-notes, paper, etc.)
4) Right- 18 inches long X 2 feet wide (Cork-board back ground with the use of push pins holding up post-it-notes, paper, etc.)
I have attached a photo of my old booth. This will get you an idea of the size, color schemes, and more. I have created basic rendering of each poster. The content is important, but the look and design should be drastically improved.
The websites to look into for ideas are:
www.kestrelforgrowth.example
www.kestrelacademy.example
Updates
I've added a new file. It's a .JPG of the certification diploma. Thanks!
Target Market(s)
Business Owners, Managers, HR, Supervisors, Teens who want to boost their resume
Industry/Entity Type
It Company
Look and feel

```html
<!DOCTYPE html>
<html lang="en">
<head>
<meta charset="utf-8">
<title>KESTREL Academy – Top Booth Banner</title>
<link href="https://fonts.googleapis.com/css2?family=Chewy&display=swap" rel="stylesheet">
<style>
  :root {
    --page-bg: #ffffff;
    --hot-pink: #ec1a5e;
    --rose: #f46a8e;
    --maroon: #7d1e2c;
    --deep-red: #a5283a;
    --sky: #7fd3f0;
    --royal: #1f4aa8;
    --navy: #142a6b;
    --blush: #fde3ea;
    --headline-fill: #ffffff;
    --headline-edge: #1b1f4a;
    --brand-ink: #142a6b;
  }
  html, body {
    margin: 0;
    padding: 0;
    width: 1200px;
    height: 172px;
    overflow: hidden;
    background: var(--page-bg);
  }
  .canvas {
    position: relative;
    width: 1200px;
    height: 172px;
  }
  .banner {
    position: absolute;
    left: 42px;
    top: 33px;
    width: 1118px;
    height: 100px;
    display: block;
  }
  .brand-name {
    font-family: "Chewy", cursive;
    font-size: 17px;
    fill: var(--brand-ink);
  }
  .headline {
    font-family: "Chewy", cursive;
    font-size: 41px;
    fill: var(--headline-fill);
    stroke: var(--headline-edge);
    stroke-width: 4px;
    stroke-linejoin: round;
    paint-order: stroke fill;
  }
</style>
</head>
<body>
<div class="canvas">
  <svg class="banner" viewBox="0 0 1118 100" xmlns="http://www.w3.org/2000/svg">
    <defs>
      <linearGradient id="top-sweep" x1="0" y1="0" x2="1" y2="0">
        <stop offset="0" stop-color="var(--hot-pink)"/>
        <stop offset="0.45" stop-color="var(--hot-pink)"/>
        <stop offset="0.75" stop-color="var(--deep-red)"/>
        <stop offset="1" stop-color="var(--maroon)"/>
      </linearGradient>
      <linearGradient id="low-sweep" x1="0" y1="0" x2="1" y2="0">
        <stop offset="0" stop-color="var(--royal)"/>
        <stop offset="1" stop-color="var(--navy)"/>
      </linearGradient>
      <radialGradient id="brand-glow" cx="0.5" cy="0.5" r="0.5">
        <stop offset="0.7" stop-color="var(--blush)"/>
        <stop offset="1" stop-color="var(--rose)"/>
      </radialGradient>
    </defs>

    <!-- banner field -->
    <rect class="field" width="1118" height="100" fill="url(#top-sweep)"/>

    <!-- lower blue wave band -->
    <path class="wave-band" d="M0 78 C250 60 500 75 700 62 C850 52 1000 48 1118 40 L1118 100 L0 100 Z" fill="url(#low-sweep)"/>
    <!-- light pink swoosh -->
    <path class="wave-light" d="M0 70 C220 60 420 72 640 58 C820 46 960 40 1118 30 L1118 38 C960 50 820 58 640 68 C420 82 220 72 0 80 Z" fill="var(--rose)" opacity="0.85"/>
    <!-- sky swoosh -->
    <path class="wave-sky" d="M0 84 C200 76 380 90 560 80 C700 72 800 74 900 70 L900 74 C780 80 700 82 560 88 C380 98 200 86 0 94 Z" fill="var(--sky)"/>
    <!-- faint upper swoosh -->
    <path class="wave-soft" d="M560 40 C760 20 940 30 1118 8 L1118 14 C940 38 760 30 560 48 Z" fill="#ffffff" opacity="0.18"/>

    <!-- brand mark area -->
    <circle class="brand-disc" cx="60" cy="50" r="47" fill="url(#brand-glow)"/>
    <text class="brand-name" x="60" y="47" text-anchor="middle">KESTREL</text>
    <text class="brand-name" x="60" y="66" text-anchor="middle">Academy</text>

    <!-- headline -->
    <text class="headline" x="146" y="62" textLength="958" lengthAdjust="spacingAndGlyphs">“The Training Solutions You’ve Been Looking For!”</text>
  </svg>
</div>
</body>
</html>
```